Rosko Tamblin

I am a songwriter and would like to include a bio, pictures, discography, CD covers and access to some of my music

Target Market(s)

Music Lovers, songwriters publishers

Coding

Coded - Design and coding required

Number of Pages Required

5+ page

Requirements
Must have
• Pictures of my CD covers, pictures of me and either my Music or links to my music
Nice to have
Should not have
• cartoons

```html
<!DOCTYPE html>
<html lang="en">
<head>
<meta charset="utf-8">
<title>Rosko Tamblin — Songwriter</title>
<link href="https://fonts.googleapis.com/css2?family=Playfair+Display:ital,wght@0,700;0,900;1,400&family=Roboto:ital,wght@0,400;0,500;0,700;1,400&display=swap" rel="stylesheet">
<style>
:root{
  --red:#a3141b;
  --red-bright:#c8161d;
  --red-dark:#7d0f14;
  --ink:#1b1b1b;
  --text:#555;
  --muted:#8a8a8a;
  --light:#f5f5f5;
  --white:#fff;
  --night:#0d0d0f;
  --blush:#f1d3d5;
}
*{box-sizing:border-box;margin:0;padding:0}
html,body{width:1200px;height:4539px;overflow:hidden}
body{position:relative;font-family:"Roboto",sans-serif;color:var(--text);background:var(--white)}
.abs{position:absolute}
.section{position:absolute;left:0;width:1200px;overflow:hidden}
.btn{position:absolute;display:flex;align-items:center;justify-content:center;gap:8px;background:var(--red-bright);color:var(--white);font:700 15px "Roboto",sans-serif;border-radius:24px;text-transform:uppercase;letter-spacing:.2px;white-space:nowrap}
.btn svg{width:14px;height:14px}
.ph{position:absolute}
.clef{position:absolute;width:60px;height:140px;border-radius:30px;background:var(--blush);opacity:.7}

/* hero */
.hero{top:0;height:601px;background:linear-gradient(100deg,#1a1614 0%,#3b2e26 35%,#6d5543 55%,#2f2c2e 75%,#151517 100%)}
.brand{position:absolute;left:111px;top:100px;display:flex;align-items:center;gap:10px;font:700 26px "Playfair Display",serif;color:var(--red-bright);text-transform:uppercase;white-space:nowrap}
.brand .dot{width:14px;height:14px;border-radius:50%;background:var(--red-bright)}
.social{position:absolute;top:36px;display:flex;gap:11px;left:652px}
.social span{width:38px;height:38px;border-radius:50%;background:var(--white)}
.nav{position:absolute;top:107px;left:0;width:1200px;font:500 15px "Roboto",sans-serif;color:var(--white)}
.nav span{position:absolute;white-space:nowrap}
.hero h1{position:absolute;left:111px;top:258px;font:900 43px/1.12 "Playfair Display",serif;color:var(--white);text-transform:uppercase}
.dots{position:absolute;display:flex;gap:8px;align-items:center}
.dots i{display:block;width:11px;height:11px;border-radius:50%;background:var(--white)}
.dots i.on{width:15px;height:15px}

/* about */
.about{top:601px;height:578px;background:var(--white)}
.about h2{position:absolute;left:624px;top:100px;font:900 38px/1.15 "Playfair Display",serif;color:var(--ink);text-transform:uppercase}
.about p{position:absolute;left:624px;top:198px;width:456px;font:15px/28.5px "Roboto",sans-serif;color:var(--muted);text-align:justify}
.divider-v{position:absolute;width:1px;background:#ddd}

/* cd covers */
.covers{top:1179px;height:835px;background:linear-gradient(180deg,#101012 0%,#2a2022 40%,#1c1718 100%)}
.title-light{position:absolute;left:0;width:1200px;text-align:center;font:900 38px "Playfair Display",serif;color:var(--white);text-transform:uppercase}
.tile{position:absolute;width:310px;background:#333}
.tile .cap{position:absolute;left:0;bottom:0;width:100%;height:33px;background:var(--red);color:var(--white);font:700 17px/33px "Roboto",sans-serif;text-align:center;text-transform:uppercase;white-space:nowrap}
.feature{position:absolute;left:111px;top:418px;width:310px;height:241px;background:var(--red-dark);color:var(--white);text-align:center}
.feature h3{margin-top:97px;font:700 20px "Roboto",sans-serif;text-transform:uppercase}
.feature p{margin:14px auto 0;width:280px;font:13px/26px "Roboto",sans-serif}

/* testimonials */
.testimonials{top:2014px;height:664px;background:var(--light)}
.eyebrow{position:absolute;left:0;width:1200px;text-align:center;font:17px "Roboto",sans-serif;color:var(--red);text-transform:uppercase}
.title-dark{position:absolute;left:0;width:1200px;text-align:center;font:900 36px "Playfair Display",serif;color:var(--ink);text-transform:uppercase}
.rule{position:absolute;left:556px;width:88px;height:3px;background:var(--red)}
.quote{position:absolute;left:83px;top:258px;width:550px;font:italic 15px/28.5px "Roboto",sans-serif;color:var(--text);text-align:justify}
.quote-mark{position:absolute;font:900 50px/1 "Playfair Display",serif;color:var(--red-bright)}
.author{position:absolute;left:83px;top:476px;font:14px "Roboto",sans-serif;color:var(--text)}
.author b{color:var(--red-bright);letter-spacing:1px;margin-left:8px}

/* gallery */
.gallery{top:2678px;height:837px;background:linear-gradient(180deg,#121214 0%,#2b2426 45%,#161314 100%)}
.shot{position:absolute;width:230px;height:236px;background:#555}
.shot .cap{position:absolute;left:0;bottom:0;width:100%;height:36px;background:var(--red);color:var(--white);font:700 17px/36px "Roboto",sans-serif;text-align:center;text-transform:uppercase}

/* discography */
.discography{top:3515px;height:652px;background:var(--white)}
.album{position:absolute;width:220px;text-align:center}
.disc{width:176px;height:176px;margin:0 auto;border-radius:50%;border:3px solid #ccc;padding:7px;background:var(--white)}
.disc .art{width:100%;height:100%;border-radius:50%;display:flex;align-items:center;justify-content:center}
.play{width:40px;height:40px;border-radius:50%;background:var(--white);display:flex;align-items:center;justify-content:center}
.album .year{margin-top:18px;font:17px "Roboto",sans-serif;color:var(--muted)}
.album h4{margin-top:8px;font:700 18px "Roboto",sans-serif;color:var(--ink);text-transform:uppercase}
.album p{margin-top:6px;font:14px "Roboto",sans-serif;color:var(--muted)}
.album .ctrl{margin-top:18px;display:flex;justify-content:center;gap:14px}
.album .ctrl span{width:28px;height:28px;border-radius:50%;border:2px solid #ccc}
.arrow{position:absolute;top:258px;width:30px;height:20px}

/* footer */
.footer{top:4167px;height:372px;background:var(--night);color:var(--white)}
.footer .brand{top:165px;font-size:28px}
.footer .about-text{position:absolute;left:111px;top:198px;width:330px;font:12.5px/19px "Roboto",sans-serif;color:#ddd}
.col{position:absolute;top:66px}
.col h5{font:700 16px "Roboto",sans-serif;color:var(--white);margin-bottom:22px;white-space:nowrap}
.col a{display:block;font:12.5px/30px "Roboto",sans-serif;color:#ddd;text-decoration:none;margin-top:-4px;white-space:nowrap}
.col p{font:12.5px/19px "Roboto",sans-serif;color:#ddd;width:190px}
.col .strong{font-weight:700;color:var(--white);margin-top:10px}
.footer hr{position:absolute;left:111px;top:309px;width:982px;border:0;border-top:1px solid #444}
.copy{position:absolute;left:0;width:1200px;top:334px;text-align:center;font:12.5px "Roboto",sans-serif;color:#ddd}
</style>
</head>
<body>

<!-- HERO -->
<header class="section hero">
  <div class="ph" role="img" aria-label="Songwriter writing notes on sheet music while holding an electric guitar" style="left:0;top:0;width:1200px;height:601px;background:radial-gradient(ellipse at 70% 45%,rgba(150,110,80,.55),rgba(0,0,0,0) 60%)"></div>
  <div class="brand"><span class="dot"></span>Rosko Tamblin</div>
  <div class="social" aria-label="Social links"><span></span><span></span><span></span><span></span></div>
  <div class="btn" style="left:860px;top:32px;width:227px;height:46px">
    <svg viewBox="0 0 14 14"><path d="M5 2v8.2A2 2 0 1 0 6.5 12V5l5-1.2v5.4A2 2 0 1 0 13 11V0z" fill="#fff"/></svg>Download Songs</div>
  <nav class="nav">
    <span style="left:465px">About Rosko Tamblin</span>
    <span style="left:668px">Gallery</span>
    <span style="left:765px">Discography</span>
    <span style="left:900px">Cd Covers</span>
    <span style="left:1017px">My Music</span>
  </nav>
  <h1>Discover the magic<br>of music</h1>
  <div class="btn" style="left:111px;top:375px;width:190px;height:48px">
    <svg viewBox="0 0 14 14"><path d="M5 2v8.2A2 2 0 1 0 6.5 12V5l5-1.2v5.4A2 2 0 1 0 13 11V0z" fill="#fff"/></svg>Get Started</div>
  <div class="dots" style="left:557px;top:551px"><i></i><i></i><i class="on"></i><i></i><i></i></div>
</header>

<!-- ABOUT -->
<section class="section about">
  <div class="clef" role="img" aria-label="Treble clef ornament" style="left:42px;top:75px"></div>
  <div class="clef" role="img" aria-label="Treble clef ornament" style="left:1104px;top:327px"></div>
  <svg class="abs" style="left:92px;top:108px" width="440" height="350" viewBox="0 0 440 350">
    <ellipse cx="222" cy="175" rx="218" ry="170" fill="#fff" stroke="#1b1b1b" stroke-width="6"/>
  </svg>
  <div class="ph" role="img" aria-label="Portrait of Rosko Tamblin in front of a glowing fiery crater" style="left:100px;top:122px;width:420px;height:320px;border-radius:50%;background:radial-gradient(ellipse at 50% 45%,#f7b23a 0%,#d9541a 40%,#6d1a0c 75%,#2a0a06 100%)"></div>
  <div class="divider-v" style="left:578px;top:83px;height:408px"></div>
  <h2>About<br>Rosko Tamblin</h2>
  <p>Rosko Tamblin was born and raised in Houston, Texas. He began playing music at the age of eight when his sister returned home from summer camp and asked her parents to buy her a baritone ukulele. She taught her younger brother some chords on the ukulele and he was hooked. The following spring, they went to one of the border towns in Mexico and bought a Mexican guitar for $12. They restrung it with nylon strings</p>
  <div class="btn" style="left:624px;top:417px;width:183px;height:46px">
    <svg viewBox="0 0 14 14"><path d="M5 2v8.2A2 2 0 1 0 6.5 12V5l5-1.2v5.4A2 2 0 1 0 13 11V0z" fill="#fff"/></svg>Learn More</div>
</section>

<!-- CD COVERS -->
<section class="section covers">
  <div class="ph" role="img" aria-label="Concert crowd under stage lights" style="left:0;top:0;width:1200px;height:835px;background:radial-gradient(ellipse at 50% 10%,rgba(120,100,110,.45),rgba(0,0,0,0) 60%)"></div>
  <h2 class="title-light" style="top:72px">CD Covers</h2>
  <div class="tile" role="img" aria-label="Album cover: The Tamblins, man playing guitar on a colourful background" style="left:111px;top:174px;height:244px;background:linear-gradient(135deg,#38d66a,#e8d34a 45%,#c94aa8 80%,#4a6ed8)"></div>
  <div class="feature">
    <svg class="abs" style="left:120px;top:28px" width="70" height="54" viewBox="0 0 70 54"><circle cx="34" cy="28" r="22" fill="none" stroke="#fff" stroke-width="2.5"/><circle cx="34" cy="28" r="8" fill="none" stroke="#fff" stroke-width="2.5"/><circle cx="34" cy="28" r="2.5" fill="#fff"/><path d="M52 8v16M52 8l10-3v14" fill="none" stroke="#fff" stroke-width="2.5"/></svg>
    <h3>The Tamblins</h3>
    <p>Lorem ipsum dolor sit amet, tetur adipiscing elit, sed do eiusmod temp cididunt ut labore et dolore magna aliqua.</p>
  </div>
  <div class="tile" role="img" aria-label="Album cover: Cal Brenner, flames with coffee cup and sugar shaker" style="left:446px;top:174px;height:227px;background:linear-gradient(160deg,#c9261a,#f07d1e 45%,#f3c66a 70%,#6a4a30)"><div class="cap">Cal Brenner</div></div>
  <div class="tile" role="img" aria-label="Album cover: Sevin Tamblor, black and white guitarist with trees" style="left:779px;top:174px;height:227px;background:linear-gradient(135deg,#2a2a2a,#8a8a8a 55%,#e0e0e0)"><div class="cap">Sevin Tamblor</div></div>
  <div class="tile" role="img" aria-label="Album cover: Changing Tides, silhouette against a stormy red sky" style="left:446px;top:430px;height:229px;background:linear-gradient(160deg,#3a4048,#7a2a1e 55%,#1a1a1a)"><div class="cap">Changing Tides</div></div>
  <div class="tile" role="img" aria-label="Album cover: When My Train Rolls In, ship on a stormy sea" style="left:779px;top:430px;height:229px;background:linear-gradient(170deg,#5c7a90,#2f4a5a 55%,#a9b7bf)"><div class="cap">When My Train Rolls In</div></div>
  <div class="btn" style="left:476px;top:698px;width:248px;height:47px">
    <svg viewBox="0 0 14 14"><path d="M5 2v8.2A2 2 0 1 0 6.5 12V5l5-1.2v5.4A2 2 0 1 0 13 11V0z" fill="#fff"/></svg>View More Cover Art</div>
</section>

<!-- TESTIMONIALS -->
<section class="section testimonials">
  <div class="clef" role="img" aria-label="Treble clef ornament" style="left:22px;top:52px"></div>
  <div class="clef" role="img" aria-label="Treble clef ornament" style="left:1112px;top:482px"></div>
  <div class="eyebrow" style="top:86px">Testimonials</div>
  <h2 class="title-dark" style="top:120px">From the Community</h2>
  <div class="rule" style="top:183px"></div>
  <div class="quote-mark" style="left:82px;top:220px">&ldquo;</div>
  <p class="quote">Yet another great song from Rosko! An unlimited catalog of excellent work. Pleasure every time Yet another great experience! 5 stars, as always. Always a great day for me when I have one of Rosko's songs on my calendar. Thoroughly enjoy each one every time! Yet another great project from Rosko! I'm amazed at the breadth of his catalog. Always enjoyable working on his music! Rosko is quickly becoming one of my favorite clients (can I say that?) Smooth process every time, friendly exchanges, and great music to work on.</p>
  <div class="quote-mark" style="left:505px;top:442px">&rdquo;</div>
  <div class="author">Mara Welling Keyboards<b>★★★★★</b></div>
  <div class="divider-v" style="left:666px;top:229px;height:303px"></div>
  <svg class="abs" style="left:692px;top:246px" width="436" height="346" viewBox="0 0 436 346"><ellipse cx="218" cy="173" rx="214" ry="168" fill="#fff" stroke="#e8e8e8" stroke-width="4"/></svg>
  <div class="ph" role="img" aria-label="Black and white halftone image of a guitarist in a hat" style="left:706px;top:256px;width:412px;height:322px;border-radius:50%;background:radial-gradient(ellipse at 45% 45%,#c8c8c8,#5a5a5a 55%,#141414 100%)"></div>
  <div class="dots" style="left:557px;top:576px"><i style="background:#ccc"></i><i style="background:#ccc"></i><i class="on" style="background:var(--red)"></i><i style="background:#ccc"></i><i style="background:#ccc"></i></div>
</section>

<!-- GALLERY -->
<section class="section gallery">
  <div class="ph" role="img" aria-label="Concert crowd with confetti" style="left:0;top:0;width:1200px;height:837px;background:radial-gradient(ellipse at 50% 5%,rgba(130,110,120,.4),rgba(0,0,0,0) 60%)"></div>
  <h2 class="title-light" style="top:75px">Our Gallery</h2>
  <div class="rule" style="top:136px;background:#fff"></div>
  <div class="shot" role="img" aria-label="Hands playing an acoustic guitar" style="left:111px;top:176px;background:linear-gradient(160deg,#3a5a78,#b58552 60%,#ddd)"><div class="cap">Magna Aliqua</div></div>
  <div class="shot" role="img" aria-label="Guitars, keyboard and studio gear seen from above" style="left:359px;top:176px;background:linear-gradient(160deg,#6b5644,#3a3a3a 55%,#8a7a6a)"><div class="cap">Magna Aliqua</div></div>
  <div class="shot" role="img" aria-label="Musician writing notes beside a guitar" style="left:608px;top:176px;background:linear-gradient(160deg,#1a1a1a,#9a8f86 55%,#eee)"><div class="cap">Magna Aliqua</div></div>
  <div class="shot" role="img" aria-label="Headphones, coffee and a CD on a wooden desk" style="left:856px;top:176px;background:linear-gradient(160deg,#e8e8e8,#7a5a3a 45%,#c9a23a)"><div class="cap">Magna Aliqua</div></div>
  <div class="shot" role="img" aria-label="Straw hat beside sheet music" style="left:111px;top:421px;background:linear-gradient(160deg,#f1efe8,#8a7a5a 55%,#c8c0b0)"><div class="cap">Magna Aliqua</div></div>
  <div class="shot" role="img" aria-label="Hands on piano keys in the dark" style="left:359px;top:421px;background:linear-gradient(160deg,#0d0d0d,#5a5a5a 55%,#bbb)"><div class="cap">Magna Aliqua</div></div>
  <div class="shot" role="img" aria-label="Hand writing lyrics with a pen next to a guitar" style="left:608px;top:421px;background:linear-gradient(160deg,#c4b38a,#8a8f80 50%,#eee)"><div class="cap">Magna Aliqua</div></div>
  <div class="shot" role="img" aria-label="Close view of fingers on guitar strings" style="left:856px;top:421px;background:linear-gradient(160deg,#d89a6a,#a5421e 55%,#5a2a1a)"><div class="cap">Magna Aliqua</div></div>
  <div class="btn" style="left:478px;top:705px;width:244px;height:46px">
    <svg viewBox="0 0 14 14"><path d="M5 2v8.2A2 2 0 1 0 6.5 12V5l5-1.2v5.4A2 2 0 1 0 13 11V0z" fill="#fff"/></svg>View More Pictures</div>
</section>

<!-- DISCOGRAPHY -->
<section class="section discography">
  <div class="clef" role="img" aria-label="Treble clef ornament" style="left:22px;top:55px"></div>
  <div class="clef" role="img" aria-label="Treble clef ornament" style="left:1110px;top:440px"></div>
  <h2 class="title-dark" style="top:80px">Discography</h2>
  <div class="rule" style="top:139px"></div>
  <svg class="arrow" style="left:58px" viewBox="0 0 30 20"><path d="M29 10H3M10 2 2 10l8 8" fill="none" stroke="#222" stroke-width="2.5"/></svg>
  <svg class="arrow" style="left:1110px" viewBox="0 0 30 20"><path d="M1 10h26M20 2l8 8-8 8" fill="none" stroke="#222" stroke-width="2.5"/></svg>

  <div class="album" style="left:105px;top:170px">
    <div class="disc"><div class="art" role="img" aria-label="Album art with man and guitar on a swirling colour background" style="background:radial-gradient(circle,#c84a3a,#6a2a8a 60%,#2a3a8a)"><span class="play"><svg width="14" height="16" viewBox="0 0 14 16"><path d="M1 0l13 8-13 8z" fill="#111"/></svg></span></div></div>
    <div class="year">2015</div><h4>Lorem Ipsum</h4><p>Lorem ipsum dolor sit amet,</p>
    <div class="ctrl"><span></span><span></span><span></span></div>
  </div>
  <div class="album" style="left:362px;top:170px">
    <div class="disc"><div class="art" role="img" aria-label="Album art with silhouette against a stormy sky" style="background:radial-gradient(circle,#8a3a2a,#3a3e48 60%,#111)"><span class="play"><svg width="14" height="16" viewBox="0 0 14 16"><path d="M1 0l13 8-13 8z" fill="#111"/></svg></span></div></div>
    <div class="year">2015</div><h4>Lorem Ipsum</h4><p>Lorem ipsum dolor sit amet,</p>
    <div class="ctrl"><span></span><span></span><span></span></div>
  </div>
  <div class="album" style="left:618px;top:170px">
    <div class="disc"><div class="art" role="img" aria-label="Album art with warm orange lettering collage" style="background:radial-gradient(circle,#d8742a,#7a2a18 60%,#2a120a)"><span class="play"><svg width="14" height="16" viewBox="0 0 14 16"><path d="M1 0l13 8-13 8z" fill="#111"/></svg></span></div></div>
    <div class="year">2015</div><h4>Lorem Ipsum</h4><p>Lorem ipsum dolor sit amet,</p>
    <div class="ctrl"><span></span><span></span><span></span></div>
  </div>
  <div class="album" style="left:873px;top:170px">
    <div class="disc"><div class="art" role="img" aria-label="Album art with vintage portrait and script titles" style="background:radial-gradient(circle,#d8cfc0,#8a8296 60%,#5a5a6a)"><span class="play"><svg width="14" height="16" viewBox="0 0 14 16"><path d="M1 0l13 8-13 8z" fill="#111"/></svg></span></div></div>
    <div class="year">2015</div><h4>Lorem Ipsum</h4><p>Lorem ipsum dolor sit amet,</p>
    <div class="ctrl"><span></span><span></span><span></span></div>
  </div>

  <div class="btn" style="left:506px;top:520px;width:188px;height:46px">
    <svg viewBox="0 0 14 14"><path d="M5 2v8.2A2 2 0 1 0 6.5 12V5l5-1.2v5.4A2 2 0 1 0 13 11V0z" fill="#fff"/></svg>Play More</div>
</section>

<!-- FOOTER -->
<footer class="section footer">
  <div class="brand"><span class="dot"></span>Rosko Tamblin</div>
  <p class="about-text">Lorem ipsum dolor sit amet, consectetur adipiscing elit, sed do eiusmod tempor incididunt</p>
  <div class="btn" style="left:111px;top:249px;width:123px;height:39px;font-size:14px;text-transform:none">Ask Question</div>
  <div class="col" style="left:513px">
    <h5>Quick Links</h5>
    <a>About Rosko Tamblin</a><a>Gallery</a><a>Discography</a><a>Cd Covers</a><a>My Music</a>
  </div>
  <div class="col" style="left:707px">
    <h5>Connect With US</h5>
    <a>Friendbook</a><a>ClipTube</a><a>Snapgram</a><a>Pinboard</a>
  </div>
  <div class="col" style="left:916px">
    <h5>Contact Us</h5>
    <p>Feel free get in touch with us via phone or send us a message</p>
    <p class="strong">555-010-2468<br>info@RoskoTamblin.com</p>
  </div>
  <hr>
  <div class="copy">Rosko Tamblin Copyright © All right reserved</div>
</footer>

</body>
</html>
```